Power Point Template Vierklang sustainability consulting

(find english description below)
We are a small German start-up that offers sustainability consulting. For presentations of results, our company presentation, proposals, lectures, etc., we need a PowerPoint template that matches our logo. We come from classic management consulting / strategy consulting and also deal with facts and figures in sustainability consulting. Therefore, the template should not be too fancy and should not only consist of photos. But it shouldn't be a completely sober template either. Our logo with the green leaves for sustainability (three leaves for VIERklang) and the white bar chart (with the dynamic swing upwards) reflects our attitude well, where we see ourselves on the range from playful to sober and classic to modern.

It might be nice for the template to include the shape of one of the leaves (from the logo). Also, the logo should appear in a corner of each slide. The colors from the logo (see appendix) should be partially reflected in the presentation. We can also imagine a gold-brown tone (see website www.vierklang-beratung.de) or a coral tone as a contrast. (Attention - the website is not final yet).

For a first suggestion, it is sufficient to suggest three to four slides (cover sheet, chapter/separation slide, text slide, data slide). We will then mark drafts that we like. In total, we would then need about 6-10 more slide templates, e.g. about us, team, slide for a statement, 2-3 data charts (pie, bar, column), top 3 - 5 list, timeline, contact (more slides are welcome ).

We are a small German start-up offering sustainability consulting. We need a power point template for result presentations, our company presentation, proposals, lectures etc. The template should be aligned with our logo. Our background lies in classic management consulting / strategy consulting and we also deal with facts and figures in sustainability consulting. Therefore, the template should not be too playful and not only consist of photos. But it should also not be a completely clear template. Our logo with the green leaves for sustainability (three leaves for VIERklang) and the white bar chart (with the dynamic upward swing) reflects our attitude well, where we see ourselves on the range from playful to down-to-earth and classic to modern .

For the template, it might be nice to incorporate the shape of one of the leaves (from the logo). Also, the logo should show up in one corner on each slide. Some of the colors from the logo (see attachment) should be reflected in the presentation. We could also think of a gold-brown tone (see website www.vierklang-beratung.de) or a coral tone for contrast. (Attention - the website is not final yet).

For a first proposal it is quite sufficient to suggest us three to four slides (cover page, chapter/separation slide, text slide, data slide). We will then mark the drafts that we like. In total we would need about 6-10 more slide templates, eg About us, Team, slide for a statement, 2-3 data charts (pie, bar, column), Top 3 - 5 List, Timeline, Contact (more slides are welcome).

Target Market(s)

Corporations, large companies and SMEs

Industry/Entity Type

Unternehmensberatung, Nachhaltigkeitsberatung

Font styles to use
Sans Serif
Other font styles liked:
• Calibri

Colors
00AB8E
00BBA5
67D7C9
C6EFE9
E9F9F6

Requirements
Must have
• see description (e.g. the colors of our logo)
Nice to have
• see description (e.g. elements of the logo included)
Should not have
• see description

```html
<!DOCTYPE html>
<html lang="en">
<head>
<meta charset="utf-8">
<title>Vierklang Consulting – Presentation Template</title>
<link href="https://fonts.googleapis.com/css2?family=Jost:wght@400;500;600;700;800&family=Open+Sans:wght@400;600&display=swap" rel="stylesheet">
<style>
:root{
  --page:#858687;
  --slide:#eeeff0;
  --slide-light:#f7f7f8;
  --ink:#111314;
  --text:#6b6d70;
  --green-dark:#3d6b1c;
  --green:#5e9127;
  --green-mid:#8cb33d;
  --green-light:#c6e07a;
  --green-accent:#8dc63f;
  --white:#ffffff;
}
*{margin:0;padding:0;box-sizing:border-box}
html,body{width:1200px;height:3909px;overflow:hidden}
body{background:var(--page);font-family:"Open Sans",Arial,sans-serif;color:var(--text);position:relative}
.slide{position:absolute;left:111px;width:978px;height:549px;overflow:hidden;
  background:
    linear-gradient(125deg,transparent 18%,rgba(255,255,255,.75) 24%,transparent 30%),
    linear-gradient(125deg,transparent 40%,rgba(255,255,255,.6) 46%,transparent 52%),
    linear-gradient(125deg,transparent 62%,rgba(255,255,255,.5) 68%,transparent 74%),
    linear-gradient(160deg,var(--slide-light),var(--slide));}
.abs{position:absolute}
.heading{font-family:"Jost",Arial,sans-serif;font-weight:700;color:var(--ink);letter-spacing:.5px}
.corner-mark{position:absolute;right:18px;bottom:18px;font-family:"Jost",Arial,sans-serif;font-weight:600;font-size:15px;color:var(--green)}
.body-copy{font-size:10.5px;line-height:20px;color:var(--text)}

/* cover */
.cover{top:106px}
.cover .brand{left:56px;top:200px;font-family:"Jost",Arial,sans-serif;font-weight:500;font-size:74px;color:#4a4d50;line-height:1}
.cover .divider{left:507px;top:167px;width:6px;height:215px;background:linear-gradient(var(--green-accent),var(--green-dark))}
.cover .title{left:543px;top:193px;font-size:50px;line-height:60px;font-weight:800}
.cover .tagline{left:545px;top:317px;font-family:"Jost",Arial,sans-serif;font-weight:600;font-size:24px;letter-spacing:3.5px;color:var(--green-accent)}

/* about */
.about{top:736px}
.about .title{left:511px;top:133px;font-size:36px}
.about .subtitle{left:513px;top:184px;font-family:"Jost",Arial,sans-serif;font-weight:600;font-size:19px;color:var(--green-accent)}
.about .copy{left:513px;width:430px}

/* charts */
.charts{top:1364px}
.charts .title{left:522px;top:36px;font-size:36px}
.charts .lead{left:522px;top:90px;width:410px;font-size:10.5px;line-height:20px}
.info-card{position:absolute;left:522px;width:387px;height:97px;background:var(--white);border-radius:14px;border-left:4px solid var(--green-dark);padding:14px 22px}
.info-card h3{font-family:"Jost",Arial,sans-serif;font-weight:700;font-size:15px;color:var(--ink);margin-bottom:4px}
.info-card p{font-size:8.4px;line-height:17px;color:#3b3d40}

/* timeline */
.timeline{top:1993px}
.timeline .title{left:0;width:978px;text-align:center;top:40px;font-size:34px}
.milestone{position:absolute;width:290px;text-align:center}
.milestone h3{font-family:"Jost",Arial,sans-serif;font-weight:600;font-size:14px;color:var(--ink);margin-bottom:6px}
.milestone p{font-size:8.6px;line-height:15px;color:#8a8c8f}
.tl-label{position:absolute;font-family:"Jost",Arial,sans-serif;font-weight:600;font-size:14px;color:var(--ink)}
.year{position:absolute;font-family:"Jost",Arial,sans-serif;font-size:13px;width:60px;text-align:center}
.year.on{color:var(--green-mid);font-weight:600}
.year.off{color:#a3a5a8}

/* team */
.team{top:2621px}
.team .title{left:0;width:978px;text-align:center;top:40px;font-size:36px}
.member{position:absolute;top:118px;width:234px}
.member .portrait{width:234px;height:192px;border-radius:0 50px 0 0;background:linear-gradient(160deg,#dfe3e6,#b9aaa0 55%,#4b5058)}
.member .nameplate{margin-top:-4px;background:var(--white);height:52px;text-align:center;padding-top:8px;box-shadow:0 2px 6px rgba(0,0,0,.06)}
.member .nameplate h3{font-family:"Jost",Arial,sans-serif;font-weight:700;font-size:15.5px;color:var(--ink)}
.member .nameplate span{font-size:9px;color:#444}
.member .bio{margin:18px auto 0;width:222px;text-align:center;font-size:9.4px;line-height:16.5px;color:#3d3f42}

/* contact */
.contact{top:3251px;background:linear-gradient(160deg,#f8f8f8,#e8e9ea)}
.contact .visual{left:0;top:0;width:589px;height:549px;background:linear-gradient(160deg,#3c4a5c,#4d6a3c 45%,#8a7a6a 75%,#33363b)}
.contact .brand{left:620px;top:28px;font-family:"Jost",Arial,sans-serif;font-weight:500;font-size:46px;color:var(--white)}
.contact .intro{left:622px;top:118px;width:322px;font-size:10.4px;line-height:18px;color:var(--white)}
.contact .kicker{left:619px;top:290px;font-family:"Jost",Arial,sans-serif;font-weight:600;font-size:12.5px;color:var(--green-mid)}
.contact .title{left:619px;top:307px;font-size:32px}
.contact-row{position:absolute;left:634px;display:flex;gap:16px;font-size:14px;line-height:26px;color:#222}
.contact-row svg{flex:none;margin-top:5px}
</style>
</head>
<body>

<!-- Cover -->
<section class="slide cover">
  <div class="abs brand">Vierklang</div>
  <div class="abs divider"></div>
  <h1 class="abs heading title">WELCOME TO<br>VIERKLANG</h1>
  <div class="abs tagline">CONSULTING</div>
  <div class="corner-mark">Vierklang</div>
</section>

<!-- About -->
<section class="slide about">
  <svg class="abs" style="left:0;top:0" width="470" height="549" viewBox="0 0 470 549" role="img" aria-label="Photo of a consultant working at a desk with a calculator and charts, in green tones">
    <defs><linearGradient id="aboutPhoto" x1="0" y1="0" x2="1" y2="1">
      <stop offset="0" stop-color="#2f5a18"/><stop offset=".55" stop-color="#6f8f2c"/><stop offset="1" stop-color="#a9a33c"/></linearGradient></defs>
    <path d="M0 70 C120 20 300 10 390 40 C440 180 420 380 280 549 L0 549 Z" fill="url(#aboutPhoto)"/>
  </svg>
  <h2 class="abs heading title">WHO ARE WE</h2>
  <div class="abs subtitle">Orientation, strategy and implementation</div>
  <p class="abs body-copy copy" style="top:220px">At Vierklang Consulting, we support companies and public institutions in anchoring and expanding sustainability in their companies – with the aim of making them more attractive, future-proof and successful.</p>
  <p class="abs body-copy copy" style="top:302px">Regardless of whether you are still at the very beginning of the process of implementing sustainability aspects in your company or whether sustainable management is already anchored in the corporate culture – we will be happy to support you with our modular offers</p>
  <div class="corner-mark">Vierklang</div>
</section>

<!-- Data charts -->
<section class="slide charts">
  <svg class="abs" style="left:0;top:0" width="510" height="549" viewBox="0 0 510 549">
    <g font-family="Jost, Arial, sans-serif" font-size="11" font-weight="600" fill="#222" text-anchor="end">
      <text x="43" y="456">0</text><text x="43" y="416">1</text><text x="43" y="377">2</text><text x="43" y="337">3</text>
      <text x="43" y="297">4</text><text x="43" y="257">5</text><text x="43" y="218">6</text><text x="43" y="178">7</text><text x="43" y="138">8</text>
    </g>
    <line x1="53" y1="130" x2="53" y2="452" stroke="#cfd1d3"/>
    <line x1="53" y1="452" x2="496" y2="452" stroke="#cfd1d3"/>
    <g>
      <rect x="82" y="186" width="21" height="266" fill="#3d6b1c"/>
      <rect x="109" y="297" width="21" height="155" fill="#c6e07a"/>
      <rect x="135" y="337" width="21" height="115" fill="#8cb33d"/>
      <rect x="190" y="297" width="21" height="155" fill="#c6e07a"/>
      <rect x="217" y="186" width="21" height="266" fill="#3d6b1c"/>
      <rect x="243" y="337" width="21" height="115" fill="#8cb33d"/>
      <rect x="302" y="249" width="21" height="203" fill="#3d6b1c"/>
      <rect x="328" y="353" width="21" height="99" fill="#8cb33d"/>
      <rect x="353" y="265" width="21" height="187" fill="#c6e07a"/>
      <rect x="408" y="174" width="21" height="278" fill="#3d6b1c"/>
      <rect x="434" y="277" width="21" height="175" fill="#8cb33d"/>
      <rect x="460" y="122" width="21" height="330" fill="#c6e07a"/>
    </g>
    <g font-family="Jost, Arial, sans-serif" font-size="12" font-weight="600" fill="#222" text-anchor="middle">
      <text x="120" y="483">2020</text><text x="228" y="483">2021</text><text x="337" y="483">2022</text><text x="443" y="483">2023</text>
    </g>
  </svg>
  <h2 class="abs heading title">DATA CHARTS</h2>
  <p class="abs lead">Lorem ipsum dolor sit amet, consectetur adipiscing elit, sed do eiusmod tempor incididunt ut labore et dolore magna aliqua. Lorem ipsum dolor sit amet, consectetur adipiscing elit, sed do eiusmod tempor</p>
  <div class="info-card" style="top:166px"><h3>LOREM IPSUM</h3><p>Lorem ipsum dolor sit amet, consectetur adipiscing elit, sed do eiusmod tempor incididunt ut labore et dolore magna aliqua. Quis ipsum suspendisse ultrices gravida. Risus commodo viverra mae</p></div>
  <div class="info-card" style="top:284px"><h3>LOREM IPSUM</h3><p>Lorem ipsum dolor sit amet, consectetur adipiscing elit, sed do eiusmod tempor incididunt ut labore et dolore magna aliqua. Quis ipsum suspendisse ultrices gravida. Risus commodo viverra mae</p></div>
  <div class="info-card" style="top:401px"><h3>LOREM IPSUM</h3><p>Lorem ipsum dolor sit amet, consectetur adipiscing elit, sed do eiusmod tempor incididunt ut labore et dolore magna aliqua. Quis ipsum suspendisse ultrices gravida. Risus commodo viverra mae</p></div>
  <div class="corner-mark">Vierklang</div>
</section>

<!-- Timeline -->
<section class="slide timeline">
  <h2 class="abs heading title">VIERKLANG TIMELINE</h2>
  <div class="milestone" style="left:222px;top:156px"><h3>Lorem Ipsum</h3><p>Lorem ipsum dolor sit amet, consectetur adipiscing elit, sed do eiusmod tempor incididunt ut labore et dolore magna aliqua. Quis ipsum suspendisse ultrices gravida. Risus commodo viverra maecenas accumsan lacus vel facilisis.</p></div>
  <div class="milestone" style="left:626px;top:156px"><h3>Lorem Ipsum</h3><p>Lorem ipsum dolor sit amet, consectetur adipiscing elit, sed do eiusmod tempor incididunt ut labore et dolore magna aliqua. Quis ipsum suspendisse ultrices gravida. Risus commodo viverra maecenas accumsan lacus vel facilisis.</p></div>
  <div class="milestone" style="left:48px;top:401px"><h3>Lorem Ipsum</h3><p>Lorem ipsum dolor sit amet, consectetur adipiscing elit, sed do eiusmod tempor incididunt ut labore et dolore magna aliqua. Quis ipsum suspendisse ultrices gravida. Risus commodo viverra maecenas accumsan lacus vel facilisis.</p></div>
  <div class="milestone" style="left:430px;top:401px"><h3>Lorem Ipsum</h3><p>Lorem ipsum dolor sit amet, consectetur adipiscing elit, sed do eiusmod tempor incididunt ut labore et dolore magna aliqua. Quis ipsum suspendisse ultrices gravida. Risus commodo viverra mae–</p></div>
  <div class="tl-label" style="left:30px;top:284px">Start</div>
  <div class="tl-label" style="left:907px;top:284px">END</div>
  <div class="year on" style="left:157px;top:266px">2020</div>
  <div class="year off" style="left:342px;top:345px">2021</div>
  <div class="year on" style="left:539px;top:270px">2022</div>
  <div class="year off" style="left:760px;top:342px">2023</div>
  <svg class="abs" style="left:0;top:0" width="978" height="549" viewBox="0 0 978 549">
    <line x1="45" y1="317" x2="926" y2="317" stroke="#9a9c9f" stroke-width="1.5"/>
    <path d="M52 312 L42 317 L52 322" fill="none" stroke="#9a9c9f" stroke-width="1.5"/>
    <path d="M919 312 L929 317 L919 322" fill="none" stroke="#9a9c9f" stroke-width="1.5"/>
    <g stroke-dasharray="2 4" stroke-width="2">
      <line x1="372" y1="244" x2="372" y2="290" stroke="#a3a5a8"/>
      <line x1="790" y1="244" x2="790" y2="290" stroke="#a3a5a8"/>
      <line x1="187" y1="344" x2="187" y2="392" stroke="#6a9a2e"/>
      <line x1="569" y1="344" x2="569" y2="392" stroke="#6a9a2e"/>
    </g>
    <circle cx="372" cy="244" r="3" fill="#a3a5a8"/><circle cx="790" cy="244" r="3" fill="#a3a5a8"/>
    <circle cx="187" cy="338" r="3" fill="#6a9a2e"/><circle cx="569" cy="338" r="3" fill="#6a9a2e"/>
    <g font-family="Jost, Arial, sans-serif" font-size="13" font-weight="600" fill="#fff" text-anchor="middle">
      <circle cx="187" cy="317" r="20" fill="#e4efcf"/><circle cx="187" cy="317" r="16" fill="#5e9127"/><text x="187" y="322">01</text>
      <circle cx="372" cy="317" r="20" fill="#e3e4e5"/><circle cx="372" cy="317" r="16" fill="#9a9c9f"/><text x="372" y="322">02</text>
      <circle cx="569" cy="317" r="20" fill="#e4efcf"/><circle cx="569" cy="317" r="16" fill="#5e9127"/><text x="569" y="322">03</text>
      <circle cx="790" cy="317" r="20" fill="#e3e4e5"/><circle cx="790" cy="317" r="16" fill="#9a9c9f"/><text x="790" y="322">04</text>
    </g>
  </svg>
  <div class="corner-mark">Vierklang</div>
</section>

<!-- Team -->
<section class="slide team">
  <h2 class="abs heading title">OUR TEAM</h2>
  <article class="member" style="left:80px">
    <div class="portrait" role="img" aria-label="Portrait photo of Dr Maren Holt"></div>
    <div class="nameplate"><h3>DR MAREN HOLT</h3><span>Managing Partners</span></div>
    <p class="bio">Maren is co-founder and managing director of Vierklang Consulting GmbH. She has a high level of analytical comprehension, thinks very far ahead and always keeps an overview of the essential issues. Maren is passionate about the topic of sustainability and can easily inspire other people with her friendly nature.</p>
  </article>
  <article class="member" style="left:373px">
    <div class="portrait" role="img" aria-label="Portrait photo of Dr Lena Brandt"></div>
    <div class="nameplate"><h3>DR LENA BRANDT</h3><span>Managing Partners</span></div>
    <p class="bio">Lena is co-founder and managing director of Vierklang Consulting GmbH. She is very good at systematically grasping complex issues and reducing them to the essentials. She thinks with foresight and develops target group-oriented solutions with foresight.</p>
  </article>
  <article class="member" style="left:664px">
    <div class="portrait" role="img" aria-label="Portrait photo of Dr Clara Wein-Oster"></div>
    <div class="nameplate"><h3>DR CLARA WEIN-OSTER</h3><span>Managing Partners</span></div>
    <p class="bio">Clara is co-founder and managing director of Vierklang Consulting GmbH. She always manages to react pragmatically and solution-oriented to changing customer requirements in dynamic project environments, without losing sight of the essentials. She has a high level of analytical comprehension and manages ...</p>
  </article>
</section>

<!-- Contact -->
<section class="slide contact">
  <div class="abs visual" role="img" aria-label="Photo of hands at a laptop overlaid with green hexagon sustainability icons"></div>
  <svg class="abs" style="left:589px;top:0" width="389" height="280" viewBox="0 0 389 280">
    <defs><linearGradient id="contactBand" x1="0" y1="0" x2="1" y2="1">
      <stop offset="0" stop-color="#4f8a22"/><stop offset="1" stop-color="#2f6214"/></linearGradient></defs>
    <path d="M0 0 H389 V205 C300 245 200 272 0 266 Z" fill="url(#contactBand)"/>
  </svg>
  <div class="abs brand">Vierklang</div>
  <p class="abs intro">Lorem ipsum dolor sit amet, consectetur adipiscing elit, sed do eiusmod tempor incididunt ut labore et dolore magna aliqua. Quis ipsum suspendisse ultrices gravida. Risus commodo viverra maecenas accumsan lacus vel facilisis. Lorem ipsum dolor sit amet, consectetur adipiscing elit, sed do eiusmod</p>
  <div class="abs kicker">VIERKLANG</div>
  <h2 class="abs heading title">THANK YOU</h2>
  <div class="contact-row" style="top:355px">
    <svg width="12" height="16" viewBox="0 0 12 16"><path d="M6 0C2.7 0 0 2.6 0 5.9 0 10 6 16 6 16s6-6 6-10.1C12 2.6 9.3 0 6 0zm0 8.3a2.4 2.4 0 1 1 0-4.8 2.4 2.4 0 0 1 0 4.8z" fill="#3d6b1c"/></svg>
    <span>Lindenhof Business Park Musterstadt<br>Ahornweg 12, 12345 Musterstadt/<br>Beispielheim</span>
  </div>
  <div class="contact-row" style="top:441px">
    <svg width="15" height="15" viewBox="0 0 16 16"><path d="M3.6 0.5l2.4 3.2-1.6 2a9 9 0 0 0 5.9 5.9l2-1.6 3.2 2.4-1.3 2.9C7.6 15.8 0.2 8.4 0.7 1.8z" fill="#3d6b1c"/></svg>
    <span>+49 (0) 1234 – 555 0199</span>
  </div>
  <div class="contact-row" style="top:481px">
    <svg width="16" height="12" viewBox="0 0 16 12"><rect width="16" height="12" rx="1.5" fill="#3d6b1c"/><path d="M1 1.5L8 7l7-5.5" fill="none" stroke="#fff" stroke-width="1.3"/></svg>
    <span>info@vierklang-beratung.de</span>
  </div>
</section>

</body>
</html>
```